Im open to ideas.. I was thinking on my business cards aswell as my logo. a place for my name. email. phone number and abn..

ive attched a file with my business logo. which i dont love the colours.. i was think a dark background with charcoal letters so something along those colour schumes but im open to ideas..

BRM Constructions

```html
<!DOCTYPE html>
<html lang="en">
<head>
<meta charset="utf-8">
<title>BRM Constructions – Business Card</title>
<link rel="stylesheet" href="https://fonts.googleapis.com/css2?family=Michroma&family=Open+Sans:wght@400&display=swap">
<style>
  :root {
    --backdrop: #1b1b1b;
    --card: #f4f4f4;
    --card-shade: #e6e6e6;
    --charcoal: #231f20;
    --red: #c8161d;
    --grey-text: #3a3a3a;
    --white: #ffffff;
  }
  * { margin: 0; padding: 0; box-sizing: border-box; }
  html, body {
    width: 1200px;
    height: 873px;
    overflow: hidden;
    background: var(--backdrop);
  }
  .stage {
    position: relative;
    width: 1200px;
    height: 873px;
  }
  .business-card {
    position: absolute;
    left: 180px;
    top: 196px;
    width: 840px;
    height: 480px;
    background: linear-gradient(160deg, var(--white) 0%, var(--card) 55%, var(--card-shade) 100%);
    box-shadow: 0 18px 40px rgba(0, 0, 0, 0.55);
    overflow: hidden;
  }
  .wordmark {
    position: absolute;
    left: 150px;
    top: 92px;
    font-family: "Michroma", sans-serif;
    font-weight: 400;
    color: var(--charcoal);
    line-height: 1;
  }
  .wordmark__name {
    display: block;
    font-size: 84px;
    letter-spacing: 2px;
  }
  .wordmark__sub {
    display: block;
    margin-top: 10px;
    font-size: 19px;
    letter-spacing: 15px;
  }
  .owner {
    position: absolute;
    right: 70px;
    top: 200px;
    text-align: right;
  }
  .owner__name {
    font-family: "Michroma", sans-serif;
    font-size: 21px;
    color: var(--red);
  }
  .owner__role {
    margin-top: 6px;
    font-family: "Open Sans", sans-serif;
    font-size: 14px;
    color: var(--grey-text);
  }
  .contact {
    position: absolute;
    left: 72px;
    top: 276px;
    list-style: none;
  }
  .contact__item {
    display: flex;
    align-items: center;
    gap: 10px;
    font-family: "Open Sans", sans-serif;
    font-size: 17px;
    color: var(--grey-text);
    margin-bottom: 10px;
  }
  .contact__icon { width: 18px; height: 18px; flex: none; }
  .contact__address {
    margin-top: 4px;
    font-family: "Michroma", sans-serif;
    font-size: 20px;
    line-height: 1.45;
    color: var(--red);
  }
  .web-band {
    position: absolute;
    left: 0;
    bottom: 0;
    width: 100%;
    height: 72px;
    background: var(--red);
    display: flex;
    align-items: center;
    justify-content: flex-end;
    padding-right: 150px;
  }
  .web-band__url {
    font-family: "Michroma", sans-serif;
    font-size: 21px;
    color: var(--white);
  }
</style>
</head>
<body>
<main class="stage">
  <article class="business-card">
    <div class="wordmark">
      <span class="wordmark__name">BRM</span>
      <span class="wordmark__sub">CONSTRUCTIONS</span>
    </div>

    <div class="owner">
      <p class="owner__name">Daniel Mercer</p>
      <p class="owner__role">Owner / Founder</p>
    </div>

    <ul class="contact">
      <li class="contact__item">
        <svg class="contact__icon" viewBox="0 0 24 24" aria-hidden="true">
          <path fill="#c8161d" d="M3 8c0-2 2-4 9-4s9 2 9 4v2h-5V8H8v2H3z"/>
          <rect x="6" y="11" width="12" height="9" rx="1.5" fill="#c8161d"/>
          <circle cx="12" cy="15.5" r="2.2" fill="#f4f4f4"/>
        </svg>
        <span>0400 555 019</span>
      </li>
      <li class="contact__item">
        <svg class="contact__icon" viewBox="0 0 24 24" aria-hidden="true">
          <rect x="2" y="5" width="20" height="14" rx="1" fill="#c8161d"/>
          <path d="M3 6l9 7 9-7" fill="none" stroke="#f4f4f4" stroke-width="1.8"/>
        </svg>
        <span>info@brmconstructions.com</span>
      </li>
      <li class="contact__address">
        48 harbour 9th st<br>
        Bayview park ny 10001
      </li>
    </ul>

    <footer class="web-band">
      <span class="web-band__url">www.brmconstructions.com</span>
    </footer>
  </article>
</main>
</body>
</html>
```